Calvanto Group Real Estate Company business cards

New business card design, we are generally happy with the basic layout of the existing front of business card, (feel free to change) but require a head shot photo on the back side.

http://www.calvanto.com.au/

Attached logos, and existing business card

------------------------------

Target Market(s)

Real estate

Industry/Entity Type

Real Estate

Contact Information for Business Card

Standard size double sided

Font styles to use
Other font styles liked:
• Futura

Requirements
Must have
• Photo head shot on the back side
Nice to have
• yes
Should not have
• No

```html
<!DOCTYPE html>
<html lang="en">
<head>
<meta charset="utf-8">
<title>Calvanto Group – Business Cards</title>
<link rel="stylesheet" href="https://fonts.googleapis.com/css2?family=Jost:wght@400;500;600&display=swap">
<style>
  :root {
    --brand-purple: #2e2360;
    --brand-orange: #f39200;
    --card-white: #ffffff;
    --page-bg: #e9e7ee;
    --photo-top: #c9ccd6;
    --photo-bottom: #3b4560;
    --rule-light: rgba(255,255,255,0.75);
  }
  * { box-sizing: border-box; margin: 0; padding: 0; }
  html, body {
    width: 1200px; height: 900px; overflow: hidden;
    background: var(--page-bg);
    font-family: "Jost", "Futura", sans-serif;
  }
  .canvas { position: relative; width: 1200px; height: 900px; }
  .card {
    position: absolute;
    width: 620px; height: 378px;
    border-radius: 4px;
    overflow: hidden;
    box-shadow: 0 10px 28px rgba(30,20,60,0.18);
  }

  /* Back card – headshot side */
  .card--back {
    left: 290px; top: 50px;
    background: var(--brand-purple);
    color: var(--card-white);
    text-align: center;
  }
  .headshot {
    position: absolute; left: 50%; top: 22px;
    width: 112px; height: 112px; margin-left: -56px;
    border-radius: 50%;
    background: radial-gradient(circle at 50% 35%, var(--photo-top) 0%, #9aa1b4 45%, var(--photo-bottom) 100%);
  }
  .back-wordmark {
    position: absolute; left: 0; right: 0; top: 146px;
    font-size: 58px; font-weight: 500; letter-spacing: 1px; line-height: 1;
    color: var(--card-white);
  }
  .services {
    position: absolute; left: 0; right: 0; top: 228px;
    font-size: 19px; font-weight: 500; letter-spacing: 0.5px;
  }
  .services .sep { color: var(--brand-orange); margin: 0 8px; }
  .services .accent { color: var(--brand-orange); }
  .tagline {
    position: absolute; left: 0; right: 0; top: 262px;
    font-size: 19px; font-weight: 500; letter-spacing: 0.5px;
  }
  .back-rule { position: absolute; height: 1px; background: var(--rule-light); }
  .back-rule--right { right: 0; width: 150px; top: 240px; }
  .back-rule--left { left: 0; width: 140px; top: 276px; }
  .back-rule--bottom { left: 0; right: 0; top: 330px; background: rgba(255,255,255,0.35); }

  /* Front card – contact side */
  .card--front {
    left: 290px; top: 472px;
    background: var(--card-white);
  }
  .front-bands { position: absolute; inset: 0; }
  .front-wordmark {
    position: absolute; left: 0; right: 0; top: 50px;
    text-align: center;
    font-size: 66px; font-weight: 500; letter-spacing: 1px; line-height: 1;
    color: var(--brand-purple);
  }
  .contact { position: absolute; color: var(--card-white); }
  .contact-lines {
    right: 262px; top: 262px; text-align: right;
    font-size: 16px; line-height: 27px; letter-spacing: 0.3px;
  }
  .contact-icons {
    left: 364px; top: 266px;
    display: flex; flex-direction: column; gap: 9px;
  }
  .contact-icons svg { width: 18px; height: 18px; fill: var(--card-white); }
  .person { left: 395px; top: 232px; }
  .person-name { font-size: 20px; font-weight: 600; line-height: 1.1; }
  .person-role { font-size: 13px; margin-top: 2px; }
  .company { left: 395px; top: 290px; }
  .company-name { font-size: 16px; font-weight: 600; }
  .company-abn { font-size: 14px; margin-top: 2px; margin-left: 14px; }
  .company-abn b { font-weight: 600; }
</style>
</head>
<body>
<main class="canvas">

  <section class="card card--back" aria-label="Business card back">
    <div class="headshot" role="img" aria-label="Headshot photo of the director"></div>
    <div class="back-wordmark">Calvanto Group</div>
    <div class="back-rule back-rule--right"></div>
    <p class="services">Buy<span class="sep">|</span><span class="accent">Sell</span><span class="sep">|</span>Rent</p>
    <p class="tagline">let us show you property</p>
    <div class="back-rule back-rule--left"></div>
    <div class="back-rule back-rule--bottom"></div>
  </section>

  <section class="card card--front" aria-label="Business card front">
    <svg class="front-bands" viewBox="0 0 620 378" width="620" height="378" aria-hidden="true">
      <polygon points="0,250 620,210 620,378 0,378" fill="var(--brand-purple)"/>
      <line x1="0" y1="241" x2="620" y2="201" stroke="var(--brand-orange)" stroke-width="5"/>
    </svg>

    <div class="front-wordmark">Calvanto Group</div>

    <div class="contact person">
      <p class="person-name">Daniel Tran</p>
      <p class="person-role">Director</p>
    </div>

    <div class="contact contact-lines">
      <p>0412 555 318</p>
      <p>daniel.tran@calvanto.com.au</p>
      <p>www.calvanto.com.au</p>
    </div>

    <div class="contact contact-icons" aria-hidden="true">
      <svg viewBox="0 0 24 24"><path d="M6.6 10.8a15.1 15.1 0 0 0 6.6 6.6l2.2-2.2a1 1 0 0 1 1-.25 11.4 11.4 0 0 0 3.6.57 1 1 0 0 1 1 1V20a1 1 0 0 1-1 1A17 17 0 0 1 3 4a1 1 0 0 1 1-1h3.5a1 1 0 0 1 1 1c0 1.25.2 2.45.57 3.57a1 1 0 0 1-.25 1z"/></svg>
      <svg viewBox="0 0 24 24"><path d="M3 5h18v14H3z M4.5 6.5 12 12l7.5-5.5" fill="none" stroke="#fff" stroke-width="2"/></svg>
      <svg viewBox="0 0 24 24"><circle cx="12" cy="12" r="9" fill="none" stroke="#fff" stroke-width="2"/><path d="M3 12h18M12 3c3 3 3 15 0 18M12 3c-3 3-3 15 0 18" fill="none" stroke="#fff" stroke-width="1.5"/></svg>
    </div>

    <div class="contact company">
      <p class="company-name">Calvanto Group</p>
      <p class="company-abn"><b>ABN:</b> 12 345 678 901</p>
    </div>
  </section>

</main>
</body>
</html>
```